Brochure about Gun Trusts

Cover Page: Image of a firearm collection or a lockbox with the title]
Headline: Protect Your Firearms Collection with a Gun Trust
Subheading: Ensure Your Legacy Remains Private and Your Wishes Are Respected
[Page 1: What is a Gun Trust?]
Definition: A legally recognized trust that allows you to collect, own, and transfer firearms, including those restricted by the KRC.
Quote: "A gun trust is a revocable trust created to hold ownership of a firearm..." - BQM
[Page 2: Benefits of a Gun Trust]
Avoid Probate: Keep your firearms out of the public probate process, maintaining your privacy.
Multi-Generational Ownership: Easily transfer ownership to beneficiaries without the need for a court proceeding.
Shared Responsibility: Allow others to legally possess and use the firearms held in the trust.
[Page 3: The Risks of Not Having a Gun Trust]
Inheritance Issues: Firearms may not be transferred as intended, potentially leading to legal complications.
Probate and Public Disclosure: Your firearms collection becomes a public record.
[Page 4: How to Set Up a Gun Trust]
Consult with an Attorney: A firearms trust attorney will create a trust that complies with all federal and state laws.
Assign a Trustee: Choose a trustee to manage the trust if you become incapacitated or pass away.
Transfer Ownership: Assign your firearms to the trust.
[Back Cover: Call to Action]
Headline: Protect Your Firearms Legacy
Contact Information: Address, Phone Number, Email, Website
Offer: Free Consultation to discuss your options

```html
<!DOCTYPE html>
<html lang="en">
<head>
<meta charset="utf-8">
<title>Gun Trust Brochure – Page Spread</title>
<link rel="stylesheet" href="https://fonts.googleapis.com/css2?family=Bebas+Neue&family=Montserrat:ital,wght@0,300;0,400;0,600;0,700;1,400&display=swap">
<style>
  :root{
    --navy:#0f1d29;
    --navy-soft:#182a3b;
    --teal:#1c4a55;
    --teal-bright:#2a5c68;
    --strip:#2d5a70;
    --ink:#ffffff;
    --photo-dark:#23292b;
    --photo-mid:#4a4843;
    --photo-warm:#6b5a3c;
  }
  *{margin:0;padding:0;box-sizing:border-box}
  html,body{width:849px;height:1200px;overflow:hidden;background:#fff}
  body{position:relative;font-family:"Montserrat",sans-serif;color:var(--ink)}
  .page{position:absolute;width:210px;height:326px;overflow:hidden;background:var(--navy);
        box-shadow:0 2px 5px rgba(0,0,0,.35)}
  .page svg.bg{position:absolute;inset:0;width:100%;height:100%}
  .page .txt{position:absolute}

  .back-cover{left:190px;top:65px}
  .front-cover{left:450px;top:65px}
  .what-is{left:192px;top:439px;background:var(--teal)}
  .benefits{left:450px;top:439px}
  .risks{left:193px;top:812px}
  .setup{left:450px;top:812px}

  .thin-title{font-weight:300;text-transform:uppercase;letter-spacing:.02em;line-height:1.05}
  .back-cover .thin-title{left:18px;top:88px;font-size:17.5px;line-height:24px}
  .back-cover .offer{left:28px;top:147px;font-size:5.6px;line-height:8px;text-transform:uppercase;width:150px}
  .back-cover .visit{left:17px;top:285px;font-size:8px;font-weight:700}
  .back-cover .web{left:17px;top:301px;display:flex;align-items:center;gap:5px;font-size:5.8px;font-weight:300}
  .web .dot{width:10px;height:10px;border-radius:50%;background:#fff;display:inline-block}

  .front-cover .headline{right:40px;top:22px;font-family:"Bebas Neue",sans-serif;font-size:23.5px;line-height:20px;text-align:right;text-transform:uppercase}
  .front-cover .subhead{left:55px;top:108px;width:115px;font-family:"Bebas Neue",sans-serif;font-size:11.5px;line-height:16.3px;text-transform:uppercase}

  .section-title{font-weight:300;font-size:14.5px;line-height:16px;text-transform:uppercase}
  .what-is .section-title{left:17px;top:20px}
  .what-is .definition{left:19px;top:68px;width:125px;font-size:8.4px;line-height:9.6px;font-weight:400}
  .what-is .quote{left:18px;top:265px;width:105px;font-size:5.3px;line-height:6.8px;font-style:italic;text-align:center;letter-spacing:.04em}

  .benefits .section-title{right:14px;top:20px;text-align:right}
  .benefits .list{right:14px;top:55px;width:120px;text-align:right;font-size:7.7px;line-height:8.9px}
  .benefits .shared{right:16px;top:259px;width:120px;text-align:right;font-size:7.7px;line-height:8.9px}
  .item-head{font-weight:700;margin-bottom:9px}
  .item-body{margin-bottom:9px;font-weight:400}

  .case-title{font-weight:300;font-size:13.6px;line-height:16px;letter-spacing:.01em}
  .risks .case-title{left:23px;top:21px}
  .risks .list{left:20px;top:57px;width:180px}
  .setup .case-title{left:17px;top:32px}
  .setup .list{left:17px;top:78px;width:180px}
  .step-head{font-size:7.4px;font-weight:700;letter-spacing:.08em;margin-bottom:8px}
  .step-body{font-size:7.6px;line-height:8.9px;letter-spacing:.06em;font-weight:400;margin-bottom:9px}
  .step-body.tight{margin-top:-8px}
</style>
</head>
<body>

<!-- Back cover -->
<section class="page back-cover">
  <svg class="bg" viewBox="0 0 210 326" aria-hidden="false">
    <defs>
      <linearGradient id="vaultTone" x1="0" y1="0" x2="1" y2="1">
        <stop offset="0" stop-color="#2a3a3a"/><stop offset=".6" stop-color="#3d3f3b"/><stop offset="1" stop-color="#6a6456"/>
      </linearGradient>
    </defs>
    <rect width="210" height="326" fill="url(#vaultTone)" role="img" aria-label="Photo of a lit display wall holding rifles and pistols with gold fittings"/>
    <polygon points="0,0 118,0 205,87 0,87" fill="var(--teal)"/>
    <polygon points="118,0 210,0 210,92" fill="var(--navy)"/>
    <line x1="199" y1="176" x2="100" y2="288" stroke="var(--navy)" stroke-width="20" stroke-linecap="round"/>
    <polygon points="0,326 0,312 80,312 70,326" fill="var(--navy)"/>
    <rect y="321" width="210" height="5" fill="var(--strip)"/>
  </svg>
  <h2 class="txt thin-title">Protect Your<br>Firearms Legacy</h2>
  <p class="txt offer">Contact us for a free consultation to discuss your options</p>
  <p class="txt visit">Visit Us :</p>
  <p class="txt web"><span class="dot"></span>www.heritagetrustcounsel.com</p>
</section>

<!-- Front cover -->
<section class="page front-cover">
  <svg class="bg" viewBox="0 0 210 326">
    <defs>
      <linearGradient id="vaultTone2" x1="0" y1="0" x2="1" y2="1">
        <stop offset="0" stop-color="#3a3c3a"/><stop offset=".55" stop-color="#5a5448"/><stop offset="1" stop-color="#1d1f1f"/>
      </linearGradient>
    </defs>
    <rect width="210" height="326" fill="url(#vaultTone2)" role="img" aria-label="Photo of a firearm collection on a pegboard wall with gold-finished rifles and pistols"/>
    <polygon points="0,0 210,0 210,90 103,196 0,113" fill="var(--navy)"/>
    <line x1="20" y1="172" x2="0" y2="192" stroke="var(--navy)" stroke-width="18" stroke-linecap="round"/>
    <rect x="174" y="45" width="6" height="17" fill="var(--teal-bright)"/>
    <rect x="174" y="65" width="6" height="17" fill="var(--teal-bright)"/>
    <rect x="174" y="85" width="6" height="17" fill="var(--teal-bright)"/>
    <rect x="174" y="105" width="6" height="12" fill="var(--teal-bright)"/>
    <rect y="321" width="210" height="5" fill="var(--strip)"/>
  </svg>
  <h1 class="txt headline">Protect Your<br>Firearms<br>Collection with a<br>Gun Trust</h1>
  <p class="txt subhead">Ensure your legacy remains private and your wishes are respected</p>
</section>

<!-- What is a gun trust -->
<section class="page what-is">
  <svg class="bg" viewBox="0 0 210 326">
    <polygon points="0,212 65,212 175,326 0,326" fill="var(--navy)"/>
    <path d="M190,0 H210 V40 Q200,40 190,28 Q180,14 190,0 Z" fill="var(--navy)"/>
    <polygon points="70,190 188,66 210,66 210,318 196,318" fill="var(--navy)"/>
    <polygon points="76,190 190,71 210,71 210,312 198,312" fill="#8d9aae" role="img" aria-label="Photo of a holstered pistol on the hip of a person in a light blue shirt"/>
    <line x1="35" y1="220" x2="75" y2="220" stroke="#fff" stroke-width=".8"/>
    <g fill="#fff">
      <circle cx="35" cy="231" r=".45"/><circle cx="40" cy="231" r=".45"/><circle cx="45" cy="231" r=".45"/><circle cx="50" cy="231" r=".45"/><circle cx="55" cy="231" r=".45"/><circle cx="60" cy="231" r=".45"/><circle cx="65" cy="231" r=".45"/><circle cx="70" cy="231" r=".45"/><circle cx="75" cy="231" r=".45"/>
      <circle cx="35" cy="237" r=".45"/><circle cx="40" cy="237" r=".45"/><circle cx="45" cy="237" r=".45"/><circle cx="50" cy="237" r=".45"/><circle cx="55" cy="237" r=".45"/><circle cx="60" cy="237" r=".45"/><circle cx="65" cy="237" r=".45"/><circle cx="70" cy="237" r=".45"/><circle cx="75" cy="237" r=".45"/>
      <circle cx="35" cy="243" r=".45"/><circle cx="40" cy="243" r=".45"/><circle cx="45" cy="243" r=".45"/><circle cx="50" cy="243" r=".45"/><circle cx="55" cy="243" r=".45"/><circle cx="60" cy="243" r=".45"/><circle cx="65" cy="243" r=".45"/><circle cx="70" cy="243" r=".45"/><circle cx="75" cy="243" r=".45"/>
      <circle cx="35" cy="249" r=".45"/><circle cx="40" cy="249" r=".45"/><circle cx="45" cy="249" r=".45"/><circle cx="50" cy="249" r=".45"/><circle cx="55" cy="249" r=".45"/><circle cx="60" cy="249" r=".45"/><circle cx="65" cy="249" r=".45"/><circle cx="70" cy="249" r=".45"/><circle cx="75" cy="249" r=".45"/>
    </g>
  </svg>
  <h2 class="txt section-title">What is a Gun<br>Trust?</h2>
  <p class="txt definition">A legally recognized trust that allows you to collect, own, and transfer firearms, including those restricted by the KRC.</p>
  <p class="txt quote">"A gun trust is a revocable trust created to hold ownership of a firearm..."<br>— BQM</p>
</section>

<!-- Benefits -->
<section class="page benefits">
  <svg class="bg" viewBox="0 0 210 326">
    <polygon points="0,70 113,187 0,310" fill="#6f7466" role="img" aria-label="Photo of a blurred grassy outdoor shooting range"/>
    <polygon points="118,192 0,310 0,326 16,326 140,206 165,226 210,182 210,162 163,208 140,190" fill="var(--teal)"/>
    <g fill="#fff">
      <circle cx="12" cy="53" r=".45"/><circle cx="17" cy="53" r=".45"/><circle cx="22" cy="53" r=".45"/><circle cx="27" cy="53" r=".45"/><circle cx="32" cy="53" r=".45"/><circle cx="37" cy="53" r=".45"/><circle cx="42" cy="53" r=".45"/><circle cx="47" cy="53" r=".45"/><circle cx="52" cy="53" r=".45"/><circle cx="57" cy="53" r=".45"/>
      <circle cx="12" cy="59" r=".45"/><circle cx="17" cy="59" r=".45"/><circle cx="22" cy="59" r=".45"/><circle cx="27" cy="59" r=".45"/><circle cx="32" cy="59" r=".45"/><circle cx="37" cy="59" r=".45"/><circle cx="42" cy="59" r=".45"/><circle cx="47" cy="59" r=".45"/><circle cx="52" cy="59" r=".45"/><circle cx="57" cy="59" r=".45"/>
      <circle cx="12" cy="65" r=".45"/><circle cx="17" cy="65" r=".45"/><circle cx="22" cy="65" r=".45"/><circle cx="27" cy="65" r=".45"/><circle cx="32" cy="65" r=".45"/><circle cx="37" cy="65" r=".45"/><circle cx="42" cy="65" r=".45"/><circle cx="47" cy="65" r=".45"/><circle cx="52" cy="65" r=".45"/><circle cx="57" cy="65" r=".45"/>
      <circle cx="12" cy="71" r=".45"/><circle cx="17" cy="71" r=".45"/><circle cx="22" cy="71" r=".45"/><circle cx="27" cy="71" r=".45"/><circle cx="32" cy="71" r=".45"/><circle cx="37" cy="71" r=".45"/><circle cx="42" cy="71" r=".45"/><circle cx="47" cy="71" r=".45"/><circle cx="52" cy="71" r=".45"/><circle cx="57" cy="71" r=".45"/>
    </g>
  </svg>
  <h2 class="txt section-title">Benefits of a Gun<br>Trust</h2>
  <div class="txt list">
    <p class="item-head">Avoid Probate:</p>
    <p class="item-body">Keep your firearms out of the public probate process, maintaining your privacy.</p>
    <p class="item-head" style="margin-bottom:4px">Multi-Generational Ownership:</p>
    <p class="item-body">Easily transfer ownership to beneficiaries without the need for a court proceeding.</p>
  </div>
  <div class="txt shared">
    <p class="item-head">Shared Responsibility:</p>
    <p class="item-body">Allow others to legally possess and use the firearms held in the trust.</p>
  </div>
</section>

<!-- Risks -->
<section class="page risks">
  <svg class="bg" viewBox="0 0 210 326">
    <defs>
      <linearGradient id="caseTone" x1="0" y1="0" x2="1" y2="1">
        <stop offset="0" stop-color="#1e2327"/><stop offset=".6" stop-color="#2a2c2c"/><stop offset="1" stop-color="#4a3a2c"/>
      </linearGradient>
    </defs>
    <rect width="210" height="326" fill="url(#caseTone)" role="img" aria-label="Photo of a pistol resting in an open foam-lined case on a wooden table"/>
    <polygon points="0,262 210,184 210,326 0,326" fill="var(--navy)"/>
    <rect y="316" width="210" height="10" fill="var(--strip)"/>
  </svg>
  <h2 class="txt case-title">The Risks of Not Having a<br>Gun Trust</h2>
  <div class="txt list">
    <p class="step-head">Inheritance Issues:</p>
    <p class="step-body">Firearms may not be transferred as intended, potentially leading to legal complications.</p>
    <p class="step-head" style="margin-top:13px">Probate and Public Disclosure:</p>
    <p class="step-body">Your firearms collection becomes a public record.</p>
  </div>
</section>

<!-- How to set up -->
<section class="page setup">
  <svg class="bg" viewBox="0 0 210 326">
    <polygon points="95,0 210,0 210,118" fill="var(--navy-soft)"/>
    <polygon points="0,242 210,193 210,326 0,326" fill="#3a434c" role="img" aria-label="Photo of several pistols and accessories laid out on a dark surface"/>
  </svg>
  <h2 class="txt case-title">How to Set Up a<br>Gun Trust</h2>
  <div class="txt list">
    <p class="step-head">Consult with an Attorney:</p>
    <p class="step-body">A firearms trust attorney will create a trust that complies with all federal and state laws.</p>
    <p class="step-head">Assign a Trustee:</p>
    <p class="step-body">Choose a trustee to manage the trust if you become incapacitated or pass away.</p>
    <p class="step-head">Transfer Ownership:</p>
    <p class="step-body tight">Assign your firearms to the trust.</p>
  </div>
</section>

</body>
</html>
```